Speisekarten-Design für gehobenes italienisches Restaurant
Zielgruppe
Wir sind ein gehobenes italienisches Restaurant und suchen ein neues Design für unsere Speisekarte. Wir haben ein eher älteres Publikum.
Aufgabenstellung
Wir möchten eine elegantes modernes Design. Einzelseiten im A4 Format.

```html
<!DOCTYPE html>
<html lang="de">
<head>
<meta charset="utf-8">
<title>Pasta – Nudelgerichte</title>
<link href="https://fonts.googleapis.com/css2?family=Open+Sans:wght@400;600;700&family=Tinos:wght@400;700&family=Mrs+Saint+Delafield&display=swap" rel="stylesheet">
<style>
  :root {
    --wine: #7a1229;
    --ink: #3f3f3f;
    --text: #555555;
    --muted: #b5b5b5;
    --paper: #ffffff;
  }
  * { margin: 0; padding: 0; box-sizing: border-box; }
  html, body { width: 848px; height: 1200px; overflow: hidden; background: var(--paper); }
  .menu-page {
    position: relative; width: 848px; height: 1200px; overflow: hidden;
    font-family: "Open Sans", Arial, sans-serif; color: var(--ink);
  }
  .page-title {
    position: absolute; left: 0; width: 848px; top: 22px; text-align: center;
    font-family: "Mrs Saint Delafield", cursive; font-size: 150px; line-height: 1;
    color: var(--wine); font-weight: 400; padding-left: 18px;
  }
  .page-subtitle {
    position: absolute; left: 0; width: 848px; top: 153px; text-align: center;
    font-family: "Tinos", "Times New Roman", serif; font-weight: 700; font-size: 23.5px;
    letter-spacing: 0.6px; color: #111;
  }
  .divider { position: absolute; background: var(--wine); }
  .divider--vertical { left: 422px; top: 226px; width: 1.5px; height: 729px; }
  .divider--left { left: 37px; top: 707px; width: 386px; height: 1.5px; }
  .divider--right { left: 423px; top: 556px; width: 388px; height: 1.5px; }
  .section-title {
    position: absolute; width: 380px; text-align: center;
    font-family: "Tinos", "Times New Roman", serif; font-weight: 400; font-size: 24px;
    letter-spacing: 0.5px; color: #111;
  }
  .dish { position: absolute; white-space: nowrap; }
  .dish__name {
    font-weight: 700; font-size: 13.6px; line-height: 18.5px; letter-spacing: 1.75px;
    color: var(--ink);
  }
  .dish__allergens {
    font-weight: 600; font-size: 8px; letter-spacing: 0.2px; color: var(--muted);
    vertical-align: 6px; margin-left: 3px; line-height: 0;
  }
  .dish__sep {
    font-weight: 400; font-size: 13px; color: var(--muted); letter-spacing: 1px;
    margin: 0 16px 0 18px; line-height: 0;
  }
  .dish__price { font-weight: 700; font-size: 12.5px; letter-spacing: 0; color: var(--wine); line-height: 0; }
  .dish__desc {
    margin-top: 2px; font-size: 10.7px; line-height: 12.9px; color: var(--text);
    letter-spacing: 0;
  }
  .footer-band {
    position: absolute; left: 0; top: 1159px; width: 848px; height: 41px; background: var(--wine);
  }
  .brand {
    position: absolute; left: 0; width: 848px; top: 1169px; text-align: center;
    font-family: "Open Sans", Arial, sans-serif; font-weight: 600; font-size: 14px;
    letter-spacing: 1.5px; color: var(--paper);
  }
</style>
</head>
<body>
<main class="menu-page">
  <h1 class="page-title">Pasta</h1>
  <p class="page-subtitle">NUDELGERICHTE</p>

  <div class="divider divider--vertical"></div>
  <div class="divider divider--left"></div>
  <div class="divider divider--right"></div>

  <h2 class="section-title" style="left:36px; top:244px;">SPAGHETTI</h2>

  <div class="dish" style="left:56px; top:302px;">
    <div class="dish__name">SPAGHETTI NAPOLI<span class="dish__allergens">Ah</span><span class="dish__sep">//</span><span class="dish__price">9,90 €</span></div>
    <p class="dish__desc">Mit leckerer Tomatensoße</p>
  </div>
  <div class="dish" style="left:56px; top:357px;">
    <div class="dish__name">SPAGHETTI AGLIO E OLIO<span class="dish__allergens">Ah</span><span class="dish__sep">//</span><span class="dish__price">11,50 €</span></div>
    <p class="dish__desc">Zubereitet mit scharfer Peperoni, Knoblauch und Olivenöl</p>
  </div>
  <div class="dish" style="left:56px; top:412px;">
    <div class="dish__name">SPAGHETTI BOLOGNESE<span class="dish__allergens">Ah, L</span><span class="dish__sep">//</span><span class="dish__price">11,90 €</span></div>
    <p class="dish__desc">Natürlich mit Hackfleisch-Soße</p>
  </div>
  <div class="dish" style="left:56px; top:466px;">
    <div class="dish__name">SPAGHETTI CARBONARA<br>ORIGINALE<span class="dish__allergens">2,3,15,C,AH</span><span class="dish__sep">//</span><span class="dish__price">14,50 €</span></div>
    <p class="dish__desc">Mit in Olivenöl geschwenktem original italienischem Guanciale und Ei</p>
  </div>
  <div class="dish" style="left:56px; top:538px;">
    <div class="dish__name">SPAGHETTI CARBONARA<br>TEDESCO<span class="dish__allergens">1,2,3,15,AH,G</span><span class="dish__sep">//</span><span class="dish__price">13,50 €</span></div>
    <p class="dish__desc">Hier die ‚eingedeutschte‘ Variante mit Schinken und Sahne-Soße</p>
  </div>
  <div class="dish" style="left:56px; top:611px;">
    <div class="dish__name">SPAGHETTI<br>FRUTTI DI MARE<span class="dish__allergens">AH,B,D,R</span><span class="dish__sep">//</span><span class="dish__price">16,90 €</span></div>
    <p class="dish__desc">Zubereitet mit Meeresfrüchten in leichter Tomatensoße</p>
  </div>

  <h2 class="section-title" style="left:36px; top:735px;">TORTELLINI</h2>
  <div class="dish" style="left:63px; top:795px;">
    <div class="dish__name">TORTELLINI<br>ALLA PANNA<span class="dish__allergens">2,3,15,G,AH</span><span class="dish__sep">//</span><span class="dish__price">12,50 €</span></div>
    <p class="dish__desc">Leckere Tortellini mit Schinken-Sahne-Soße</p>
  </div>

  <h2 class="section-title" style="left:444px; top:244px;">LINGUINE</h2>
  <div class="dish" style="left:455px; top:305px;">
    <div class="dish__name">LINGUINE MEDITERRANO<span class="dish__allergens">G,AH</span><span class="dish__sep">//</span><span class="dish__price">13,50 €</span></div>
    <p class="dish__desc">Nudel-Spezialität zubereitet mit frischen Cocktailtomaten,<br>Mozzarella-Käse, einem Hauch Knoblauch, Rucola und<br>on top frisch gehobelte Scheiben vom Parmesan-Käse</p>
  </div>
  <div class="dish" style="left:455px; top:385px;">
    <div class="dish__name">LINGUINE MIT<br>FLUSSKREBSEN<span class="dish__allergens">B,G,AH</span><span class="dish__sep">//</span><span class="dish__price">15,50 €</span></div>
    <p class="dish__desc">Köstliche Variante mit Flusskrebsen in Safran-Sahne-Soße</p>
  </div>
  <div class="dish" style="left:455px; top:458px;">
    <div class="dish__name">LINGUINE SALMONE<span class="dish__allergens">D,G,AH</span><span class="dish__sep">//</span><span class="dish__price">16,90 €</span></div>
    <p class="dish__desc">Feine Nudeln mit frischem nordischen Lachs, Schalotten,<br>Knoblauch und Cocktailtomaten an rosa Tomaten-Sahne-Soße</p>
  </div>

  <h2 class="section-title" style="left:441px; top:580px;">PENNE</h2>
  <div class="dish" style="left:462px; top:635px;">
    <div class="dish__name">PENNE AMATRICIANA<span class="dish__allergens">2,3,15,AH</span><span class="dish__sep">//</span><span class="dish__price">12,90 €</span></div>
    <p class="dish__desc">Mit Zwiebeln, Speck und Cocktailtomaten<br>in leckerer Tomatensoße, pikant zubereitet</p>
  </div>
  <div class="dish" style="left:462px; top:703px;">
    <div class="dish__name">PENNE DI MANZO<span class="dish__allergens">AH,G,PP</span><span class="dish__sep">//</span><span class="dish__price">19,90 €</span></div>
    <p class="dish__desc">Mit gebratenen argentinischen Rumpsteakstreifen,<br>mit Kirschtomaten in San-Marzano Tomatensoße<br>getoppt von frischem Basilikum und 36 Monate<br>gereiftem Parmigiano Reggiano sowie gerösteten Pinienkernen</p>
  </div>
  <div class="dish" style="left:462px; top:796px;">
    <div class="dish__name">PENNE ARRABBIATA<span class="dish__allergens">6,AH</span><span class="dish__sep">//</span><span class="dish__price">13,50 €</span></div>
    <p class="dish__desc">Feines Nudelgericht mit Zwiebeln, Cocktailtomaten<br>und Oliven in Tomatensoße. Scharf zubereitet</p>
  </div>
  <div class="dish" style="left:462px; top:864px;">
    <div class="dish__name">PENNE ALLA CHEF<span class="dish__allergens">AH,B,C,D,G,L</span><span class="dish__sep">//</span><span class="dish__price">17,50 €</span></div>
    <p class="dish__desc">Aufwartend mit Lachs und Shrimps<br>in rosa Tomaten-Sahne-Soße serviert</p>
  </div>

  <footer class="footer-band"></footer>
  <p class="brand">Osteria Marrano</p>
</main>
</body>
</html>
```